International professional tennis coach needs a book cover design

This is my 2nd published book, the first one was a #1 on the best seller. I'm looking for a world class book cover design for this new book. The name of my first book was 5 Baseline Habits to Unlock Your Flow Rhythm, located on Bookvale.com

The title of the new book:

Title: The Craft of Rally Mastery
Subtitle: Building a Tactical Edge through Match Data Insight

I'm uploading our new CRAFT OF RALLY logo that I'd like for you to use as the centerpiece of the book design along with a 21st century design feel that incorporates what the book topic is below::

--> This book is about building competitive intelligence by using tennis data analytics to develop and expand a player's strategic advantage for match play. <--

The colors we would like to use are Blue, Yellow, and Green. These shades of these colors should be bold! (You will see the bold color examples of blues, yellows, and greens that I'm talking about in the logos that are attached here, especially the colors for my Racket GridDrill App logo.

I will upload the Racket GridDrill logo which should go somewhere on the back cover design (small size maybe in the bottom corner).

This book is revolutionary to the standard way of teaching tennis, it is based on a decade of recording and gathering tennis data analytics and then we created on-court practice games to develop better decision making in players for the competitive edge.

My websites are www.elevatedrillzone.com and www.craftofrallymastery.com

```html
<!DOCTYPE html>
<html lang="en">
<head>
<meta charset="utf-8">
<title>The Craft of Rally Mastery – Book Cover</title>
<link rel="stylesheet" href="https://fonts.googleapis.com/css2?family=Great+Vibes&family=Playfair+Display:wght@400;600;700&display=swap">
<style>
  :root {
    --page-bg: #e9e9e6;
    --cover-white: #fdfdfc;
    --cover-shade: #f1f1ef;
    --title-green: #2e8a34;
    --band-green: #1c7a1f;
    --rule-green: #8cc63f;
    --mark-blue: #1e88d0;
    --ink: #1f1f1f;
    --white: #ffffff;
  }
  * { box-sizing: border-box; margin: 0; padding: 0; }
  html, body {
    width: 1200px;
    height: 800px;
    overflow: hidden;
    background: var(--page-bg);
  }
  .stage {
    width: 1200px;
    height: 800px;
    display: flex;
    align-items: center;
    justify-content: center;
  }
  .book-cover {
    position: relative;
    width: 490px;
    height: 760px;
    background: linear-gradient(160deg, var(--cover-white) 0%, var(--cover-shade) 100%);
    box-shadow: 0 10px 30px rgba(0,0,0,0.18);
    display: flex;
    flex-direction: column;
    align-items: center;
    overflow: hidden;
  }
  .title {
    margin-top: 30px;
    text-align: center;
    color: var(--title-green);
    line-height: 0.95;
    font-weight: normal;
  }
  .title-script {
    display: block;
    font-family: "Great Vibes", cursive;
    font-size: 74px;
    line-height: 1;
    margin-bottom: -10px;
  }
  .title-main {
    display: block;
    font-family: "Playfair Display", serif;
    font-weight: 600;
    font-size: 84px;
    letter-spacing: -1px;
  }
  .logo-mark {
    margin-top: 62px;
    display: flex;
    align-items: center;
    gap: 14px;
    color: var(--mark-blue);
    font-family: "Playfair Display", serif;
    font-weight: 700;
    font-size: 36px;
    letter-spacing: 2px;
  }
  .logo-dot {
    width: 24px;
    height: 24px;
    border-radius: 50%;
    background: var(--mark-blue);
    flex: none;
  }
  .subtitle {
    margin-top: 62px;
    width: 410px;
    padding: 14px 0;
    border-top: 1px solid var(--rule-green);
    border-bottom: 1px solid var(--rule-green);
    text-align: center;
    font-family: "Playfair Display", serif;
    font-size: 23px;
    line-height: 1.3;
    color: var(--ink);
    letter-spacing: 0.5px;
  }
  .author-band {
    position: absolute;
    left: 0;
    right: 0;
    bottom: 0;
    height: 76px;
    background: var(--band-green);
    display: flex;
    align-items: center;
    justify-content: center;
    font-family: "Playfair Display", serif;
    font-weight: 700;
    font-size: 25px;
    color: var(--white);
    letter-spacing: 0.5px;
    white-space: nowrap;
  }
</style>
</head>
<body>
  <main class="stage">
    <article class="book-cover">
      <h1 class="title">
        <span class="title-script">The Craft of</span>
        <span class="title-main">RALLY</span>
        <span class="title-main">MASTERY</span>
      </h1>
      <div class="logo-mark">
        <span class="logo-dot"></span>
        <span class="logo-name">CRAFT OF RALLY</span>
      </div>
      <p class="subtitle">Building a Tactical Edge<br>through Match Data Insight</p>
      <footer class="author-band">Marlow Kessington &amp; Reid Halvorsen</footer>
    </article>
  </main>
</body>
</html>
```